Brightfen Business Card Redesign & Logo Update

We need to update our business cards to something more modern and fresh. Brightfen can provide the current color schemes and old design examples, but welcome creativity in helping us with this redesign. PLEASE NOTE that we no longer utilize the "tree" and/or "leaf" imagery in our branding. If able would apprecaite an update on the quality of our "words only" logo in Ai. / PNG formats too.

Target Market(s)

Investors, landowners, corporate partners, contractors

Industry/Entity Type

Environmental Restoration & Conservation

Contact Information for Business Card

Logo, persons name, title, mailing address, phone and email, website url

Font styles to use
Other font styles liked:
• Merriweather

Requirements
Nice to have
• Logo, persons name, title, mailing address, phone and email, website url, but open to ideams
Should not have
• No all back backgrounds

```html
<!DOCTYPE html>
<html lang="en">
<head>
<meta charset="utf-8">
<title>Brightfen Business Card</title>
<link rel="stylesheet" href="https://fonts.googleapis.com/css2?family=Montserrat:wght@400;500;700&display=swap">
<style>
  :root {
    --orange: #ec7f24;
    --green: #167c3e;
    --ink: #1c1c1c;
    --white: #ffffff;
    --backdrop: #e4e4e4;
  }
  * { box-sizing: border-box; margin: 0; padding: 0; }
  html, body { width: 1200px; height: 856px; overflow: hidden; }
  body {
    background: var(--backdrop);
    display: flex;
    align-items: center;
    justify-content: center;
    gap: 40px;
    font-family: "Montserrat", sans-serif;
  }
  .card {
    width: 540px;
    height: 309px;
    position: relative;
    box-shadow: 0 10px 24px rgba(0,0,0,0.22);
  }
  .card-front {
    background: var(--white);
    border-bottom: 3px solid var(--orange);
  }
  .card-back {
    background: var(--orange);
    display: flex;
    align-items: center;
    justify-content: center;
  }
  .brand {
    display: flex;
    align-items: center;
    font-family: "Montserrat", sans-serif;
    font-weight: 700;
    line-height: 1;
  }
  .brand-dot {
    border-radius: 50%;
    flex-shrink: 0;
  }
  .front-brand {
    position: absolute;
    top: 34px;
    right: 30px;
    gap: 10px;
    font-size: 34px;
    color: var(--green);
  }
  .front-brand .brand-dot { width: 16px; height: 16px; background: var(--green); }
  .back-brand {
    gap: 16px;
    font-size: 60px;
    color: var(--white);
  }
  .back-brand .brand-dot { width: 28px; height: 28px; background: var(--white); }
  .address {
    position: absolute;
    top: 128px;
    right: 30px;
    text-align: right;
    font-style: normal;
    font-size: 12px;
    line-height: 1.5;
    color: var(--ink);
  }
  .person {
    position: absolute;
    top: 130px;
    left: 30px;
  }
  .person-name {
    font-weight: 700;
    font-size: 17px;
    text-transform: uppercase;
    letter-spacing: 0.5px;
  }
  .person-name .first { color: var(--green); }
  .person-name .last { color: var(--orange); }
  .person-title { font-size: 12.5px; color: var(--ink); margin-top: 3px; }
  .contact-list {
    position: absolute;
    left: 30px;
    bottom: 28px;
    list-style: none;
  }
  .contact-item {
    display: flex;
    align-items: center;
    gap: 10px;
    font-size: 13px;
    color: var(--ink);
    margin-top: 7px;
  }
  .contact-icon {
    width: 20px;
    height: 20px;
    border-radius: 50%;
    background: var(--orange);
    display: flex;
    align-items: center;
    justify-content: center;
    flex-shrink: 0;
  }
</style>
</head>
<body>
  <section class="card card-front" aria-label="Business card front">
    <div class="brand front-brand">
      <span class="brand-dot"></span>
      <span class="brand-name">Brightfen</span>
    </div>
    <address class="address">
      42-10 Alder Street 8<br>
      Ridgeway, NY 11290
    </address>
    <div class="person">
      <div class="person-name"><span class="first">Dana</span> <span class="last">Keller</span></div>
      <div class="person-title">Managing Director</div>
    </div>
    <ul class="contact-list">
      <li class="contact-item">
        <span class="contact-icon">
          <svg width="11" height="11" viewBox="0 0 24 24" fill="#fff"><path d="M6.6 10.8a15 15 0 0 0 6.6 6.6l2.2-2.2c.3-.3.7-.4 1-.2 1.1.4 2.3.6 3.6.6.6 0 1 .4 1 1V20c0 .6-.4 1-1 1A17 17 0 0 1 3 4c0-.6.4-1 1-1h3.5c.6 0 1 .4 1 1 0 1.3.2 2.5.6 3.6.1.3 0 .7-.2 1z"/></svg>
        </span>
        555-214-3360
      </li>
      <li class="contact-item">
        <span class="contact-icon">
          <svg width="11" height="11" viewBox="0 0 24 24" fill="none" stroke="#fff" stroke-width="2.4"><rect x="3" y="6" width="18" height="12"/><path d="M3 6l9 7 9-7"/></svg>
        </span>
        info@brightfen.com
      </li>
      <li class="contact-item">
        <span class="contact-icon">
          <svg width="11" height="11" viewBox="0 0 24 24" fill="none" stroke="#fff" stroke-width="2.2"><circle cx="12" cy="12" r="9"/><path d="M3 12h18M12 3c3 3 3 15 0 18M12 3c-3 3-3 15 0 18"/></svg>
        </span>
        www.brightfen.com
      </li>
    </ul>
  </section>

  <section class="card card-back" aria-label="Business card back">
    <div class="brand back-brand">
      <span class="brand-dot"></span>
      <span class="brand-name">Brightfen</span>
    </div>
  </section>
</body>
</html>
```